Dental Practice Billboard Design

We are a newer dental practice in need of a simple but appealing billboard for our growing dental practice to attract new patients. The practice is owned by husband and wife dentists and is family friendly in a small town in Kentucky. We try to be very friendly and caring to our patients. Would prefer a blue background for the billboard and our tooth logo to be prominent. We are partial to the Patua One font used in the image below but please feel free to tweak it as you deem necessary. The shape of the uppercase D and lowercase g are why we like that font, so fonts with a similarly shaped “D” and “g” would work as well. Please include our phone number (555) 847-1390. Please see our website Harlowbrookdentistry.example for more info on the practice if needed. Thank you! Looking forward to seeing your creation.
Updates

The dimensions will be 12ft x 24ft (3.6576m x 7.3152m). Apologies for not including this in the original prompt. Thank you all for your submissions.

Industry/Entity Type

Dental

Font styles to use
Other font styles liked:
• Patua One

Colors
0054AA
0677BA
7BADD7
CADEEF
E8F1F8
0094D4
00A9DD
6FCCEA
C7EBF8
E9F6FB
00AB8E
00BBA5
67D7C9
C6EFE9
E9F9F6
59FF00
82FF00
B8FF75
E3FFCB
F4FFEA

Requirements
Must have
• Phone number, website, Logo, Practice name “Harlow Brook Dentistry”
Should not have
• A tagline or slogan

```html
<!DOCTYPE html>
<html lang="en">
<head>
<meta charset="utf-8">
<title>Harlow Brook Dentistry Billboard</title>
<link href="https://fonts.googleapis.com/css2?family=Patua+One&family=Fira+Sans+Condensed:wght@600&display=swap" rel="stylesheet">
<style>
  :root {
    --navy: #022058;
    --green: #1dbb0a;
    --white: #ffffff;
    --mist: #e8f1f8;
    --ink: #0b2a63;
  }
  * { margin: 0; padding: 0; box-sizing: border-box; }
  html, body {
    width: 1200px;
    height: 722px;
    overflow: hidden;
    background: var(--white);
  }
  .billboard {
    position: relative;
    width: 1200px;
    height: 722px;
    background: var(--navy);
    overflow: hidden;
    font-family: "Patua One", Georgia, serif;
  }
  .brand {
    position: absolute;
    left: 0;
    top: 0;
    width: 1200px;
    height: 604px;
    display: flex;
    align-items: center;
    justify-content: center;
    gap: 48px;
  }
  .brand-mark {
    flex: none;
    width: 210px;
    height: 210px;
    border-radius: 50%;
    background: var(--green);
  }
  .brand-name {
    font-size: 118px;
    line-height: 1.05;
    color: var(--white);
    font-weight: 400;
  }
  .brand-name span { display: block; }
  .contact-bar {
    position: absolute;
    left: 0;
    bottom: 0;
    width: 1200px;
    height: 118px;
  }
  .bar-shapes {
    position: absolute;
    inset: 0;
  }
  .phone {
    position: absolute;
    left: 34px;
    top: 0;
    height: 118px;
    display: flex;
    align-items: center;
    gap: 16px;
  }
  .phone-icon {
    width: 62px;
    height: 62px;
    border-radius: 50%;
    background: var(--navy);
    display: flex;
    align-items: center;
    justify-content: center;
  }
  .phone-number {
    font-family: "Fira Sans Condensed", "Arial Narrow", sans-serif;
    font-weight: 600;
    font-size: 76px;
    color: var(--white);
    letter-spacing: -1px;
  }
  .website {
    position: absolute;
    left: 652px;
    top: 0;
    height: 118px;
    display: flex;
    align-items: center;
    gap: 14px;
    color: var(--ink);
    font-size: 32px;
  }
</style>
</head>
<body>
  <main class="billboard">
    <div class="brand">
      <span class="brand-mark"></span>
      <h1 class="brand-name"><span>Harlow Brook</span><span>Dentistry</span></h1>
    </div>

    <div class="contact-bar">
      <svg class="bar-shapes" width="1200" height="118" viewBox="0 0 1200 118" aria-hidden="true">
        <rect x="0" y="0" width="1200" height="118" fill="var(--mist)"/>
        <polygon points="0,0 596,0 632,59 596,118 0,118" fill="var(--navy)"/>
        <polygon points="0,0 574,0 610,59 574,118 0,118" fill="var(--green)"/>
      </svg>
      <div class="phone">
        <span class="phone-icon">
          <svg width="34" height="34" viewBox="0 0 24 24" aria-hidden="true">
            <path fill="#ffffff" d="M6.6 10.8a15.1 15.1 0 0 0 6.6 6.6l2.2-2.2a1 1 0 0 1 1-.25 11.4 11.4 0 0 0 3.6.57 1 1 0 0 1 1 1V20a1 1 0 0 1-1 1A17 17 0 0 1 3 4a1 1 0 0 1 1-1h3.5a1 1 0 0 1 1 1c0 1.25.2 2.45.57 3.57a1 1 0 0 1-.25 1z"/>
          </svg>
        </span>
        <span class="phone-number">(555) 847-1390</span>
      </div>
      <div class="website">
        <svg width="44" height="36" viewBox="0 0 46 38" aria-hidden="true">
          <rect x="7" y="3" width="32" height="24" rx="2" fill="none" stroke="var(--ink)" stroke-width="4"/>
          <rect x="1" y="30" width="44" height="6" rx="2" fill="var(--ink)"/>
        </svg>
        <span class="website-url">Harlowbrookdentistry.example</span>
      </div>
    </div>
  </main>
</body>
</html>
```